Long webpage to explain and sell a complex concept

Accountancy firm wishes to explain Management Accounting to a Small Business audience. We have written the text, assembled a couple of charts and quotes and some concept photos.
There is a lot of text and it is required to explain this type of accounting.
Rather than have a long single block of text which is less likely to be read, we want to break it up with pictures, appropriate white space, diagrams etc. Someone landing on this page will then scroll down reading the text which is designed to keep you reading more.
The page on the website where this will go is https://www.brindlequay.com.au/services/management-accountants-perth/
So the fonts/colours need to fit in. Notice there is a pallet of colours which can be seen here: https://www.brindlequay.com.au/services/

Target Market(s)

Small Business owners in Perth, Western Australia

Number of Pages Required

1 page

Requirements
Must have
• The look and feel needs to match the website indicated in the description above. However we're happy to make the design of this page more interesting than the rest of the site.

```html
<!DOCTYPE html>
<html lang="en">
<head>
<meta charset="utf-8">
<title>Management Accounting – Confidence in your numbers</title>
<link href="https://fonts.googleapis.com/css2?family=Lora:wght@400;700&family=Open+Sans:wght@300;400&family=Cinzel:wght@400&display=swap" rel="stylesheet">
<style>
:root{
  --olive:#6b6a1f;
  --plum:#6a1b6e;
  --ink:#3f3f3f;
  --rule:#8a8a5a;
  --navy:#0b4f70;
  --cocoa:#4a3a33;
  --white:#ffffff;
  --sky-top:#2e7fc4;
  --sky-low:#a9cbe8;
}
*{margin:0;padding:0;box-sizing:border-box}
html,body{width:1200px;height:3161px;overflow:hidden;background:var(--white)}
.page{position:relative;width:1200px;height:3161px}
.abs{position:absolute}
.section-title{font-family:"Open Sans",sans-serif;font-weight:300;font-size:37px;line-height:53px}
.title-confidence{left:193px;top:120px;width:337px;text-align:right;color:var(--olive)}
.title-stress{left:669px;top:1884px;width:400px;color:var(--plum)}
.divider{width:1px;background:var(--rule)}
.body-copy{font-family:"Lora",serif;font-size:19px;line-height:38.6px;color:var(--ink);text-align:justify}
.body-copy p+p{margin-top:38.6px}
.body-copy strong{font-weight:700;color:#222}
.photo-sky{background:linear-gradient(180deg,var(--sky-top) 0%,#5b9bd3 35%,var(--sky-low) 60%,#3f73ac 100%)}
.photo-dart{background:radial-gradient(circle at 60% 50%,#f3e3b4 0%,#8fb6cf 25%,#3f78a8 60%,#1d4f7d 100%)}
.photo-person{background:linear-gradient(135deg,#a67a52 0%,#6b4a33 45%,#c7a37d 100%)}
.predict-list{list-style:disc;margin-left:42px}
.predict-list ul{list-style:none;margin-left:0}
.predict-list ul li{position:relative;padding-left:30px}
.predict-list ul li::before{content:"o";position:absolute;left:0}
.banner-aim{left:144px;top:1202px;width:908px;height:57px;background:var(--navy);color:var(--white);font-family:"Cinzel",serif;font-size:52px;line-height:57px;text-align:center;letter-spacing:5px}
.chart-card{left:182px;top:2088px;width:403px;height:258px;border:1px solid #ddd;background:var(--white)}
.footer-band{left:0;top:2924px;width:1200px;height:183px;background:var(--cocoa);color:var(--white);font-family:"Cinzel",serif;font-size:45px;line-height:52px;letter-spacing:5px;text-align:center;padding-top:40px}
</style>
</head>
<body>
<main class="page">

  <h2 class="abs section-title title-confidence">Confidence<br>in your numbers</h2>
  <div class="abs divider" style="left:586px;top:86px;height:174px"></div>

  <div class="abs body-copy" style="left:193px;top:292px;width:393px">
    <p>If you are reviewing you numbers monthly (and you should be), but you're not sure just how accurate they are, and you have to do lots of checking and fixing to have some confidence in them, you're unlikely to persist with your regular reporting.</p>
    <p>Having professional bookkeepers and accountants oversea and prepare your management reports will give you the confidence to trust the reports freeing you up to analyse your business and make decisions.</p>
  </div>

  <div class="abs photo-sky" role="img" aria-label="Glass skyscraper rising into a blue sky" style="left:611px;top:331px;width:557px;height:378px"></div>
  <div class="abs photo-dart" role="img" aria-label="Dart striking the bullseye of a dartboard against the sky" style="left:63px;top:788px;width:533px;height:358px"></div>

  <div class="abs body-copy" style="left:618px;top:838px;width:396px;text-align:left">
    <p style="text-align:justify">From this you can make two powerful predictions with some simple maths:</p>
    <ul class="predict-list">
      <li>How much profit you will make by the end of the year if
        <ul>
          <li>you hit budget for the rest of the year</li>
          <li>things continue the way they've been going</li>
        </ul>
      </li>
    </ul>
  </div>

  <div class="abs banner-aim">“YOU GET WHAT YOU AIM AT”</div>

  <div class="abs body-copy" style="left:193px;top:1312px;width:393px">
    <p style="text-align:left">Early warning</p>
    <p>If things aren't going well, you will know that your planned profit will be looking sad, so now you can take action with plenty of time on your side to make the changes you need to make. An "early warning system", if you like. As they say in aviation : "There's nothing more useless than altitude above you, or runway behind you". The earlier you know that something is wrong, the faster you fix it, the more likely you will preserve your profit.</p>
  </div>

  <div class="abs photo-sky" role="img" aria-label="Glass skyscraper rising into a blue sky" style="left:611px;top:1353px;width:557px;height:378px"></div>

  <div class="abs divider" style="left:612px;top:1849px;height:173px;background:#333"></div>
  <h2 class="abs section-title title-stress">Lower Stress<br>levels</h2>

  <div class="abs chart-card">
    <svg width="403" height="258" viewBox="0 0 330 211" font-family="Open Sans, sans-serif">
      <text x="165" y="15" font-size="7" fill="#666" text-anchor="middle">Forecast</text>
      <g stroke="#e3e3e3" stroke-width="0.6">
        <line x1="30" y1="27" x2="322" y2="27"/><line x1="30" y1="49.7" x2="322" y2="49.7"/>
        <line x1="30" y1="72.4" x2="322" y2="72.4"/><line x1="30" y1="95.1" x2="322" y2="95.1"/>
        <line x1="30" y1="117.8" x2="322" y2="117.8"/><line x1="30" y1="140.5" x2="322" y2="140.5"/>
        <line x1="30" y1="163" x2="322" y2="163"/><line x1="30" y1="185" x2="322" y2="185"/>
      </g>
      <g font-size="4.5" fill="#666" text-anchor="end">
        <text x="27" y="29">300,000</text><text x="27" y="51.5">250,000</text>
        <text x="27" y="74">200,000</text><text x="27" y="97">150,000</text>
        <text x="27" y="119.5">100,000</text><text x="27" y="142">50,000</text>
        <text x="27" y="165">0</text><text x="27" y="187">-50,000</text>
      </g>
      <g font-size="4.5" fill="#666" text-anchor="middle">
        <text x="44" y="172">Jul 19</text><text x="68" y="172">Aug 19</text><text x="92" y="172">Sep 19</text>
        <text x="116" y="172">Oct 19</text><text x="140" y="172">Nov 19</text><text x="165" y="172">Dec 19</text>
        <text x="189" y="172">Jan 20</text><text x="213" y="172">Feb 20</text><text x="237" y="172">Mar 20</text>
        <text x="261" y="172">Apr 20</text><text x="285" y="172">May 20</text><text x="309" y="172">Jun 20</text>
      </g>
      <polyline fill="none" stroke="#1aa7e0" stroke-width="1.2" points="44,97.2 68,90.4 92,67.7 116,99.4 140,79 165,79 189,67.7 213,72.2 237,67.7 261,79 285,81.3 309,51.8"/>
      <polyline fill="none" stroke="#7cc94a" stroke-width="1.2" points="44,99.4 68,95.8 92,95.8 116,95.8 140,83.6 165,95.8 189,95.8 213,95.8 237,95.8 261,95.8 285,83.6 309,95.8"/>
      <polyline fill="none" stroke="#e0201b" stroke-width="1.2" points="44,160.7 68,156.2 92,133.5 116,165.3 140,158.5 165,144.8 189,135.8 213,139.4 237,134.9 261,145.7 285,160.7 309,117.6"/>
      <g font-size="4.5" fill="#666">
        <line x1="98" y1="198" x2="112" y2="198" stroke="#1aa7e0" stroke-width="1.2"/><text x="113" y="199.5">Income</text>
        <line x1="142" y1="198" x2="156" y2="198" stroke="#7cc94a" stroke-width="1.2"/><text x="157" y="199.5">All Expenses</text>
        <line x1="196" y1="198" x2="210" y2="198" stroke="#e0201b" stroke-width="1.2"/><text x="211" y="199.5">Net Profit</text>
      </g>
    </svg>
  </div>

  <div class="abs body-copy" style="left:613px;top:2074px;width:393px;text-align:left">
    <p>Here's how it works. Do you know that feeling when you look at your profit figure for the month and your heart sinks, because it's low, or even negative?</p>
    <p>Recall the real budget forecast above:</p>
  </div>

  <div class="abs body-copy" style="left:196px;top:2394px;width:393px">
    <p>Now if you had predicted a loss for a particular month, and the Budget vs Actual report showed the expected loss (and all other numbers roughly in line with expectation), then you know that you are <strong>on track for your desired profit</strong> (at least for that month anyway). Don't you feel a whole lot better about that?</p>
    <p>So now the management reports are <strong>focusing you on what you really need to know about,</strong> clearing away the noise you don't need to worry about.</p>
  </div>

  <div class="abs photo-person" role="img" aria-label="Relaxed business owner smiling on a sofa while reading a tablet" style="left:613px;top:2450px;width:504px;height:335px"></div>

  <div class="abs footer-band">"BUDGET FORECASTING MAKES CLEAR,<br>WHAT YOU NEED TO FOCUS ON"</div>

</main>
</body>
</html>
```